Kelumo.cn needs pages to be re-designed

www.kelumo.cn is our current new site which was launched in April.
We're a financial services website in the crowdfunding space in China to connect borrower's and lender's.

test.kelumo.cn is our test site
u: test
p: newtest
http://test.kelumo.cn/
http://test.kelumo.cn/user/accounts/new_lender
http://test.kelumo.cn/user/accounts/new_borrower
http://test.kelumo.cn/introductions/protection
http://test.kelumo.cn/introductions
http://test.kelumo.cn/introductions/kelumo_admin
http://test.kelumo.cn/introductions/contact
Some of the pages have pop-ups in the bloc's of the pages. Please click the links, to see more content.

User's currently criticize the website for being:
- Too Western looking
- Too simple, too little content
- Content NOT in the pop-ups are too simple
- Pictures are too big and too much blank space
- Relevant information is not there when needed
- The pictures are too generic

What we would like to do is re-design those pages with the same color scheme and style to be more compelling, efficient, non-intimidating and easy-to-use. Our audience is Ages 25-35 predominantly male investors.
We are looking for more ideas to make the content match the style, while bridging western and chinese design. Our ultimate goal is to increase registrants to the website and highlight our core competitive advantages.

Some competitors websites are:
www.fobuxiqi.com
www.tamev.com
www.zzzlendo.com

Reason: Not enough good designs that follow the prompt. Same style, better information layout!

Reason: Still have not received a design we're satisfied with

Reason: WE DONT WANT A COMPLETE REDESIGN OF PAGES . KEEP THE EXACT SAME COLOR AND STYLE - WE WANT CONTENT RE-DESIGN! THE BLOCS ARE TOO SIMPLE - WE WANT MORE CONTENT INSIDE.

Reason: no new designs

Reason: no new designs

Reason: other non-registered pages need to be re-designed

```html
<!DOCTYPE html>
<html lang="zh-CN">
<head>
<meta charset="utf-8">
<title>Kelumo.cn 投资</title>
<link href="https://fonts.googleapis.com/css2?family=Noto+Sans+SC:wght@400;500;700&display=swap" rel="stylesheet">
<style>
:root{
  --green:#6cb83a;
  --green-dark:#4f9a24;
  --blue:#2a8fd6;
  --blue-light:#5cb4ee;
  --dark:#3b3b3b;
  --text:#555;
  --muted:#999;
  --panel:#f1f2f3;
  --white:#fff;
}
*{margin:0;padding:0;box-sizing:border-box}
html,body{width:1200px;height:3325px;overflow:hidden}
body{font-family:"Noto Sans SC",sans-serif;color:var(--text);background:var(--white);position:relative;font-size:14px}
.site-header{height:80px;display:flex;align-items:center;justify-content:space-between;padding:0 70px 0 100px;border-bottom:1px solid #e4e4e4}
.brand{display:flex;align-items:center;gap:12px;font-size:26px;font-weight:700;color:var(--green)}
.brand-dot{width:40px;height:40px;border-radius:50%;background:var(--green)}
.brand small{display:block;font-size:11px;font-weight:700;color:var(--green);line-height:1}
.main-nav{display:flex;gap:46px;font-size:15px}
.main-nav a{color:var(--text);text-decoration:none;display:flex;align-items:center;gap:8px}
.main-nav a::before{content:"";width:14px;height:14px;border-radius:3px;background:#9a9a9a}
.main-nav a.active{color:var(--green)}
.main-nav a.active::before{background:var(--green)}
.hero{height:490px;background:linear-gradient(120deg,#c9d5df 0%,#eef2f5 45%,#dfe6ec 70%,#aeb9c2 100%)}
.feature-bar{height:62px;background:var(--dark);display:flex;justify-content:center}
.feature-bar a{color:#fff;text-decoration:none;font-size:22px;display:flex;align-items:center;gap:12px;padding:0 38px;border-right:1px solid #555}
.feature-bar a:last-child{border-right:0}
.feature-bar svg{width:26px;height:26px}
.overview{height:798px;position:relative}
.overview h2{position:absolute;top:50px;width:100%;text-align:center;font-size:28px;font-weight:500;color:#444}
.overview svg.flow{position:absolute;top:90px;left:0}
.flow text{font-family:"Noto Sans SC",sans-serif}
.overview .tail{position:absolute;top:730px;width:100%;display:flex;justify-content:center;gap:180px;font-size:17px;color:var(--blue)}
.overview .tail span{border-bottom:2px solid var(--blue);padding-bottom:4px}
.benefits{height:1280px;background:var(--panel);padding:40px 70px 0;display:grid;grid-template-columns:1fr 1fr;grid-auto-rows:400px;gap:20px 60px}
.card{position:relative}
.card-title{display:flex;align-items:center;gap:14px;font-size:26px;color:#444;border-bottom:1px solid #ddd;padding-bottom:12px;margin-bottom:18px}
.card-icon{width:44px;height:44px;border:3px solid var(--blue);border-radius:6px;display:flex;align-items:center;justify-content:center;color:var(--blue);font-size:20px;font-weight:700}
.card h4{font-size:16px;color:#333;margin-bottom:10px}
.card p{font-size:13px;line-height:1.9;color:var(--muted);width:190px}
.card svg.art{position:absolute;right:0;top:80px}
.card .art text{font-family:"Noto Sans SC",sans-serif}
.rate-table{position:absolute;left:40px;top:270px;border-collapse:collapse;font-size:12px;color:var(--text)}
.rate-table th,.rate-table td{padding:6px 18px;text-align:center}
.rate-table th{border-bottom:1px solid #ccc;font-weight:500}
.btn-small{position:absolute;left:210px;top:370px;background:var(--blue);color:#fff;font-size:12px;padding:4px 14px;border-radius:3px}
.safety{height:440px;position:relative}
.safety-head{position:absolute;left:130px;top:30px;display:flex;align-items:center;gap:12px;font-size:24px;color:#444;background:#fff;padding-right:16px;z-index:1}
.safety-box{position:absolute;left:100px;right:100px;top:55px;height:290px;border:3px solid var(--blue-light);border-radius:14px;display:grid;grid-template-columns:1fr 1fr;padding:42px 40px 0}
.safety-col{display:flex;gap:40px}
.safety-col h5{font-size:22px;color:#444;font-weight:500;margin-top:80px;width:110px;text-decoration:underline;white-space:nowrap}
.safety-col ul{list-style:none;font-size:14px;color:var(--text);line-height:2.1}
.safety-col li::before{content:"";display:inline-block;width:10px;height:10px;border:1px solid var(--blue);margin-right:10px}
.safety-col .more{display:block;margin-top:6px;color:var(--blue);font-size:14px;text-decoration:underline}
.cta{position:absolute;left:50%;top:385px;transform:translateX(-50%);display:flex;align-items:center;gap:14px;background:var(--blue);color:#fff;font-size:24px;padding:8px 44px 8px 8px;border-radius:30px;white-space:nowrap}
.cta::before{content:"";width:40px;height:40px;border-radius:50%;background:#fff}
.partners{height:95px;padding:15px 170px;display:flex;align-items:center;gap:40px;border-top:1px solid #e4e4e4}
.partners h6{font-size:14px;color:#444;font-weight:500;white-space:nowrap}
.partners i{display:block;width:140px;height:30px;background:#e1e1e1;border-radius:3px}
.site-footer{height:80px;background:#8c8c8c;display:flex;align-items:center;justify-content:space-between;padding:0 80px;color:#eee;font-size:14px}
.site-footer .icons{display:flex;gap:18px}
.site-footer .icons i{width:30px;height:30px;border-radius:50%;background:#b3b3b3;display:block}
</style>
</head>
<body>
<header class="site-header">
  <div class="brand"><span class="brand-dot"></span><div>Kelumo<small>kelumo.cn</small></div></div>
  <nav class="main-nav"><a>首页</a><a class="active">投资</a><a>借款</a><a>关于</a><a>登录 ▾</a></nav>
</header>

<section class="hero" role="img" aria-label="手握笔在纸上画灯泡与房屋草图的照片"></section>

<nav class="feature-bar">
  <a><svg viewBox="0 0 26 26"><rect x="3" y="3" width="20" height="20" rx="2" fill="none" stroke="#fff" stroke-width="2"/><path d="M8 13l4 4 7-8" fill="none" stroke="#fff" stroke-width="2"/></svg>风控</a>
  <a><svg viewBox="0 0 26 26"><rect x="3" y="7" width="20" height="14" rx="2" fill="#fff"/><circle cx="13" cy="14" r="3" fill="#3b3b3b"/></svg>保护金</a>
  <a><svg viewBox="0 0 26 26"><path d="M3 13h8M15 5h8M15 21h8M11 13l4-8M11 13l4 8" stroke="#fff" stroke-width="2" fill="none"/></svg>分散</a>
  <a><svg viewBox="0 0 26 26"><circle cx="19" cy="6" r="3.5" fill="#fff"/><circle cx="19" cy="20" r="3.5" fill="#fff"/><circle cx="6" cy="13" r="3.5" fill="#fff"/><path d="M6 13L19 6M6 13l13 7" stroke="#fff" stroke-width="2"/></svg>资金安全</a>
  <a><svg viewBox="0 0 26 26"><path d="M13 3l9 4v6c0 6-4 9-9 11-5-2-9-5-9-11V7z" fill="#fff"/></svg>责任</a>
</nav>

<section class="overview">
  <h2>6 标题範例</h2>
  <svg class="flow" width="1200" height="640" viewBox="0 0 1200 640">
    <defs>
      <g id="person"><circle cx="0" cy="-9" r="7" fill="#8a8a8a"/><path d="M-11 12a11 11 0 0 1 22 0z" fill="#8a8a8a"/></g>
    </defs>
    <path d="M340 70V40H980V60" stroke="var(--green)" stroke-width="4" fill="none"/>
    <text x="600" y="30" text-anchor="middle" font-size="15" fill="#666">標題範例</text>
    <use href="#person" x="340" y="155"/>
    <text x="370" y="165" font-size="12" fill="#777">示例文本</text>
    <line x1="390" y1="120" x2="700" y2="120" stroke="#ccc" stroke-width="1"/>
    <text x="520" y="114" font-size="15" fill="#555">2. 每年: 示例文本每</text>
    <text x="905" y="100" font-size="15" fill="#555">1. 每年: 示例文本每</text>
    <line x1="905" y1="108" x2="1060" y2="108" stroke="var(--blue)" stroke-width="2"/>
    <line x1="985" y1="120" x2="985" y2="270" stroke="#ccc"/>
    <use href="#person" x="985" y="140"/><text x="1005" y="145" font-size="11" fill="#777">示例文本</text>
    <use href="#person" x="985" y="180"/><text x="1005" y="185" font-size="11" fill="#777">示例文本</text>
    <use href="#person" x="985" y="220"/><text x="1005" y="225" font-size="11" fill="#777">示例文本</text>
    <use href="#person" x="985" y="260"/><text x="1005" y="265" font-size="11" fill="#777">示例文本</text>
    <path d="M340 175V315H985V290" stroke="#555" stroke-width="4" fill="none"/>
    <text x="600" y="305" text-anchor="middle" font-size="15" fill="#555">標題範例</text>
    <path d="M155 315V505H330" stroke="#555" stroke-width="4" fill="none"/>
    <path d="M155 315h185" stroke="#555" stroke-width="4"/>
    <line x1="155" y1="420" x2="330" y2="420" stroke="#555" stroke-width="4"/>
    <line x1="600" y1="315" x2="600" y2="555" stroke="#555" stroke-width="4"/>
    <path d="M590 555h20l-10 12z" fill="#555"/>
    <text x="520" y="420" font-size="15" fill="#555">3. 每年: 標題範例標題範例</text>
    <line x1="520" y1="428" x2="700" y2="428" stroke="var(--blue)" stroke-width="2"/>
    <text x="520" y="505" font-size="15" fill="#555">4. 每年: 標題範例標題範例</text>
    <line x1="520" y1="513" x2="700" y2="513" stroke="var(--blue)" stroke-width="2"/>
    <circle cx="790" cy="492" r="14" fill="var(--green)"/>
    <text x="812" y="497" font-size="14" fill="#555">Qiaofeng Life</text>
    <text x="918" y="497" font-size="18" fill="#555">+</text>
    <text x="940" y="497" font-size="14" fill="#555">Borvane 博安保险经纪</text>
    <rect x="525" y="575" width="150" height="30" rx="3" fill="#555"/>
    <text x="600" y="596" text-anchor="middle" font-size="13" fill="#fff">了解详情</text>
  </svg>
  <div class="tail"><span>5. 每年: 標題範例標題範例標題範例</span><span>6. 每年: 標題範例標題範例標題範例</span></div>
</section>

<section class="benefits">
  <article class="card">
    <div class="card-title"><span class="card-icon">1</span>1, 风控</div>
    <h4>標本標題樣本標題</h4>
    <p>我们对每一笔借款进行严格审核，包括身份验证、收入证明与信用记录，确保借款人具备按时还款能力，为出借人提供安全保障。</p>
    <svg class="art" width="300" height="260" viewBox="0 0 300 260">
      <path d="M40 20h220l-25 38H65z" fill="#1e6fb6"/>
      <path d="M65 62h170l-25 38H90z" fill="#2a8fd6"/>
      <path d="M90 104h120l-25 38H115z" fill="#4fa7dd"/>
      <path d="M115 146h70l-20 38h-30z" fill="#6cb83a"/>
      <path d="M137 188h26l-13 38z" fill="#4f9a24"/>
      <text x="150" y="44" text-anchor="middle" font-size="11" fill="#fff">申请</text>
      <text x="150" y="86" text-anchor="middle" font-size="11" fill="#fff">审核</text>
      <text x="150" y="128" text-anchor="middle" font-size="11" fill="#fff">评估</text>
      <text x="150" y="170" text-anchor="middle" font-size="11" fill="#fff">批准</text>
    </svg>
  </article>

  <article class="card">
    <div class="card-title"><span class="card-icon">2</span>2, 分数</div>
    <h4>標本標題樣本標題</h4>
    <p>将资金分散投资给多位借款人，降低单笔违约带来的影响，让收益更加稳定。</p>
    <svg class="art" width="330" height="300" viewBox="0 0 330 300">
      <defs><g id="pp"><circle cx="0" cy="-9" r="7" fill="#8a8a8a"/><path d="M-11 12a11 11 0 0 1 22 0z" fill="#8a8a8a"/></g></defs>
      <use href="#pp" x="40" y="150"/>
      <text x="20" y="185" font-size="12" fill="var(--blue)">¥ 1000</text>
      <path d="M60 150H150M150 30V270M150 30h90M150 90h90M150 150h90M150 210h90M150 270h90" stroke="#ccc" fill="none"/>
      <use href="#pp" x="255" y="30"/><text x="275" y="35" font-size="11" fill="var(--blue)">¥ 200</text>
      <use href="#pp" x="255" y="90"/><text x="275" y="95" font-size="11" fill="var(--blue)">¥ 200</text>
      <use href="#pp" x="255" y="150"/><text x="275" y="155" font-size="11" fill="var(--blue)">¥ 200</text>
      <use href="#pp" x="255" y="210"/><text x="275" y="215" font-size="11" fill="var(--blue)">¥ 200</text>
      <use href="#pp" x="255" y="270"/><text x="275" y="275" font-size="11" fill="var(--blue)">¥ 200</text>
    </svg>
  </article>

  <article class="card">
    <div class="card-title"><span class="card-icon">3</span>3, 保护金</div>
    <h4>標題範例</h4>
    <p>平台提取风险保护金，当借款逾期时先行垫付本金，保障出借人权益。</p>
    <svg class="art" width="240" height="180" viewBox="0 0 240 180" style="right:40px;top:90px">
      <circle cx="100" cy="90" r="70" fill="none" stroke="#e3e3e3" stroke-width="26"/>
      <circle cx="100" cy="90" r="70" fill="none" stroke="var(--green)" stroke-width="26" stroke-dasharray="260 440" transform="rotate(-90 100 90)"/>
      <circle cx="100" cy="90" r="70" fill="none" stroke="var(--blue)" stroke-width="26" stroke-dasharray="90 440" stroke-dashoffset="-260" transform="rotate(-90 100 90)"/>
      <text x="185" y="40" font-size="11" fill="#777">保护金</text>
      <text x="185" y="150" font-size="11" fill="#777">本金</text>
    </svg>
    <table class="rate-table">
      <tr><th></th><th>示例文本</th><th>示例文本</th><th>示例文本</th></tr>
      <tr><td>1年</td><td>100% 示例</td><td>示例</td><td>示例文本</td></tr>
      <tr><td>1-2年</td><td>100% 示例</td><td>示例</td><td>示例文本</td></tr>
      <tr><td>2-3年</td><td>100% 示例</td><td>示例</td><td>示例文本</td></tr>
    </table>
    <span class="btn-small">了解详情</span>
  </article>

  <article class="card">
    <div class="card-title"><span class="card-icon">4</span>4, 将您的风险</div>
    <h4>每示例文本每年示例文本</h4>
    <svg class="art" width="540" height="280" viewBox="0 0 540 280" style="top:110px">
      <defs><g id="pq"><circle cx="0" cy="-9" r="7" fill="#8a8a8a"/><path d="M-11 12a11 11 0 0 1 22 0z" fill="#8a8a8a"/></g></defs>
      <path d="M60 60L270 150M60 240L270 150M480 60L270 150M480 240L270 150" stroke="#d5d5d5" stroke-dasharray="4 4"/>
      <circle cx="270" cy="150" r="30" fill="var(--green)"/>
      <rect x="240" y="195" width="60" height="18" fill="#e0e0e0"/>
      <rect x="240" y="218" width="60" height="18" fill="#e0e0e0"/>
      <use href="#pq" x="60" y="60"/><text x="30" y="90" font-size="11" fill="#777">示例文本</text>
      <use href="#pq" x="60" y="240"/><text x="30" y="270" font-size="11" fill="#777">示例文本</text>
      <use href="#pq" x="480" y="240"/><text x="455" y="270" font-size="11" fill="#777">示例文本</text>
      <circle cx="450" cy="55" r="8" fill="var(--green)"/>
      <text x="464" y="59" font-size="11" fill="#555">Borvane</text>
    </svg>
  </article>

  <article class="card">
    <div class="card-title"><span class="card-icon">5</span>5, 资金安全</div>
    <h4>资金安全</h4>
    <p>出借资金由第三方支付机构托管，平台不触碰用户资金，每一笔交易均可查询，全程透明可追溯。</p>
    <svg class="art" width="260" height="260" viewBox="0 0 260 260">
      <line x1="100" y1="10" x2="100" y2="200" stroke="#ccc"/>
      <rect x="20" y="40" width="160" height="26" fill="#d9c8a8"/>
      <rect x="20" y="80" width="160" height="26" fill="#b89a6a"/>
      <rect x="20" y="120" width="160" height="26" fill="#8a6a3a"/>
      <rect x="20" y="160" width="160" height="26" fill="#5c4422"/>
      <text x="190" y="58" font-size="11" fill="#777">示例文本</text>
      <text x="190" y="98" font-size="11" fill="#777">示例文本</text>
      <text x="190" y="138" font-size="11" fill="#777">示例文本</text>
      <text x="190" y="178" font-size="11" fill="#777">示例文本</text>
      <rect x="60" y="215" width="90" height="24" rx="3" fill="var(--blue)"/>
      <text x="105" y="232" text-anchor="middle" font-size="11" fill="#fff">了解详情</text>
    </svg>
  </article>

  <article class="card">
    <div class="card-title"><span class="card-icon">6</span>6, 将您的风险</div>
    <h4>资金安全</h4>
    <p>平台系统部署于专业云服务商，数据多重备份加密存储，支付通道与多家持牌机构合作，保障资金流转。</p>
    <svg class="art" width="230" height="260" viewBox="0 0 230 260">
      <text x="10" y="30" font-size="18" fill="#555">Yunshan Hosting</text>
      <text x="10" y="70" font-size="13" fill="#555">资金托管账户</text>
      <line x1="10" y1="80" x2="200" y2="80" stroke="#ddd"/>
      <rect x="20" y="100" width="22" height="22" fill="#c8c8c8"/><text x="56" y="117" font-size="13" fill="#555">托管机构 A</text>
      <rect x="20" y="145" width="22" height="22" fill="#c8c8c8"/><text x="56" y="162" font-size="13" fill="#555">托管机构 B</text>
      <rect x="20" y="190" width="22" height="22" fill="#c8c8c8"/><text x="56" y="207" font-size="13" fill="#555">托管机构 C</text>
    </svg>
  </article>
</section>

<section class="safety">
  <div class="safety-head"><svg width="34" height="34" viewBox="0 0 26 26"><path d="M13 3l9 4v6c0 6-4 9-9 11-5-2-9-5-9-11V7z" fill="var(--blue)"/></svg>资金安全</div>
  <div class="safety-box">
    <div class="safety-col">
      <h5>将您的风险</h5>
      <div>
        <ul>
          <li>该信息将帮助我们评估借款风险</li><li>该信息将帮助我们评估借款风险</li><li>该信息将帮助我们评估借款风险</li>
          <li>该信息将帮助我们评估借款风险</li><li>该信息将帮助我们评估借款风险</li><li>该信息将帮助我们评估借款风险</li>
        </ul>
        <a class="more">更多保护</a>
      </div>
    </div>
    <div class="safety-col">
      <h5>将您的</h5>
      <div>
        <ul>
          <li>该信息将帮助我们评估借款风险</li><li>该信息将帮助我们评估借款风险</li><li>该信息将帮助我们评估借款风险</li>
          <li>该信息将帮助我们评估借款风险</li><li>该信息将帮助我们评估借款风险</li><li>该信息将帮助我们评估借款风险</li>
        </ul>
        <a class="more">更多保护</a>
      </div>
    </div>
  </div>
  <div class="cta">开始投资</div>
</section>

<section class="partners">
  <h6>合作伙伴</h6>
  <i></i><i></i><i></i><i></i><i></i>
</section>

<footer class="site-footer">
  <span>© Kelumo.cn 版权所有</span>
  <div class="icons"><i></i><i></i><i></i><i></i></div>
</footer>
</body>
</html>
```